Bry7Legal Letterhead

Need a new letterhead for my law firm.
IDENTIFYING INFORMATION BELOW:
Anselmo R Quintara III
Attorney at Law
Address: 2847 Larkspur Blvd, Ste 300, Dallas, TX 75204
Phone: 877-482-6017
Fax: 469-738-1452
Email: bry@bry7legal.example
Website: www.bry7legal.example

Colors
0054AA
0677BA
7BADD7
CADEEF
E8F1F8

Requirements
Must have
• Logo needs to be on the letterhead, along with identifying information which is included in the project description.

```html
<!DOCTYPE html>
<html lang="en">
<head>
<meta charset="utf-8">
<title>Bry7Legal Letterhead</title>
<link rel="stylesheet" href="https://fonts.googleapis.com/css2?family=Arimo:wght@400;700&display=swap">
<style>
  :root {
    --backdrop: #e8e9ea;
    --paper: #ffffff;
    --ink: #1a1a1a;
    --brand-deep: #0054aa;
    --brand-mid: #0677ba;
    --brand-light: #1e9ad8;
    --rule-dark: #111111;
  }
  * { margin: 0; padding: 0; box-sizing: border-box; }
  html, body {
    width: 1200px; height: 874px; overflow: hidden;
    background: var(--backdrop);
    font-family: "Arimo", Arial, sans-serif;
    color: var(--ink);
  }
  .letterhead {
    position: absolute; left: 303px; top: 17px;
    width: 594px; height: 840px;
    background: var(--paper);
    box-shadow: 0 4px 18px rgba(0,0,0,.12);
    overflow: hidden;
  }
  .brand {
    position: absolute; left: 55px; top: 34px;
    display: flex; align-items: center; gap: 10px;
  }
  .brand-mark {
    width: 14px; height: 14px; background: var(--brand-mid);
  }
  .brand-name {
    font-size: 34px; font-weight: 700; letter-spacing: 1px;
    color: var(--ink); text-transform: uppercase;
  }
  .contact {
    position: absolute; left: 420px; top: 30px;
    padding-left: 14px;
    border-left: 1px solid var(--brand-mid);
    font-size: 8.5px; line-height: 13px;
  }
  .contact-item { display: flex; align-items: center; gap: 5px; white-space: nowrap; }
  .contact-item svg { width: 8px; height: 8px; fill: var(--brand-mid); flex: none; }
  .letter {
    position: absolute; left: 55px; top: 168px; width: 490px;
    font-size: 11.5px; line-height: 16px;
  }
  .recipient { margin-bottom: 4px; }
  .letter p { margin-bottom: 22px; }
  .closing { margin-top: -6px; }
  .signature {
    width: 120px; height: 60px; margin-top: 10px;
    background: linear-gradient(90deg, #f3f3f3, #e6e6e6);
  }
  .corner { position: absolute; left: 0; top: 0; }
  .corner-address {
    position: absolute; left: 432px; top: 781px;
    transform: rotate(-12.4deg); transform-origin: left top;
    color: #fff; font-size: 10.5px; line-height: 14px; text-align: center;
  }
</style>
</head>
<body>
<main class="letterhead">
  <header>
    <div class="brand">
      <span class="brand-name">Bry7Legal</span>
      <span class="brand-mark"></span>
    </div>
    <div class="contact">
      <div class="contact-item"><svg viewBox="0 0 10 10"><path d="M2 0h2l1 3-1.5 1a6 6 0 0 0 2.5 2.5L7 5l3 1v2c0 1-1 2-2 2A8 8 0 0 1 0 2c0-1 1-2 2-2z"/></svg>877-482-6017</div>
      <div class="contact-item"><svg viewBox="0 0 10 10"><path d="M2 0h6v3H2zM0 3h10v5H8v2H2V8H0zM3 6v3h4V6z"/></svg>469-738-1452</div>
      <div class="contact-item"><svg viewBox="0 0 10 10"><path d="M0 2h10v1L5 6 0 3zM0 4l5 3 5-3v4H0z"/></svg>bry@bry7legal.example</div>
      <div class="contact-item"><svg viewBox="0 0 10 10"><circle cx="5" cy="5" r="5"/></svg>www.bry7legal.example</div>
    </div>
  </header>

  <section class="letter">
    <div class="recipient">Mr/s<br>First Name and Last Name<br>Company Name<br>Address</div>
    <p>Lorem Ipsum is simply dummy text of the printing and typesetting industry. Lorem Ipsum has been the industry's standard dummy text ever since the 1500s, when an unknown printer took a galley of type and scrambled it to make a type specimen book. It has survived not only five centuries, but also the leap into electronic typesetting, remaining essentially unchanged. It was popularised in the 1960s.</p>
    <p>The standard chunk of Lorem Ipsum used since the 1500s is reproduced below for those interested. Sections 1.10.32 and 1.10.33 from "de Finibus Bonorum et Malorum" by Cicero are also reproduced in their exact original form, accompanied by English versions from the 1914 translation by H. Rackham. Lorem ipsum dolor sit amet, consectetur adipiscing elit, sed do eiusmod tempor incididunt ut labore et dolore magna aliqua.</p>
    <p>It is a long established fact that a reader will be distracted by the readable content of a page when looking at its layout. The point of using Lorem Ipsum is that it has a more-or-less normal distribution of letters, as opposed to using 'Content here, content here', making it look like readable English. Many desktop publishing packages and web page editors now .</p>
    <div class="closing">Your Sincerely,</div>
    <div class="signature" role="img" aria-label="Handwritten signature"></div>
  </section>

  <svg class="corner" width="594" height="840" viewBox="0 0 594 840">
    <defs>
      <linearGradient id="cornerBlue" x1="0" y1="1" x2="1" y2="0">
        <stop offset="0" stop-color="var(--brand-light)"/>
        <stop offset="1" stop-color="var(--brand-deep)"/>
      </linearGradient>
    </defs>
    <polygon points="548,752 130,840 140,840 552,754" fill="var(--rule-dark)"/>
    <polygon points="594,743 594,840 154,840" fill="url(#cornerBlue)"/>
  </svg>
  <div class="corner-address">2847 Larkspur Blvd, Ste<br>300, Dallas, TX 75204</div>
</main>
</body>
</html>
```